Modern Business Card for Larkwell 2018

Our company assumes the best about people. We are creating an online community of entrepreneurs and business leaders who struggle with marketing their business online.

This business card should POP! We recently got a new logo and are launching a new website next month, so our business cards should make a statement that feels:
-Fresh
-Smart
-Trustworthy
-Fun

Target Market(s)

small business owners, entrepreneurs

Industry/Entity Type

Digital Marketing

Contact Information for Business Card

Dimensions: 3.5" x 2"

Font styles to use
Sans Serif

Colors
f37122
ffffff

Requirements
Must have
• We need a business card with a modern, bold design. We will use one side of the card as a lead-generation offer, so text on one side will need to fit up to 140 characters. The business card should stick to our core colors (orange, black, and white).
Nice to have
• We think a vertical "portrait" design could be interesting.
Should not have
• Should not look like a traditional business card. The round icon should stand out from a distance.

```html
<!DOCTYPE html>
<html lang="en">
<head>
<meta charset="utf-8">
<title>Larkwell Business Card</title>
<link rel="stylesheet" href="https://fonts.googleapis.com/css2?family=Montserrat:wght@600;700&family=Permanent+Marker&family=Fira+Sans:ital,wght@0,400;0,500;1,500&family=Roboto:wght@500;700&display=swap">
<style>
:root{
  --orange:#f37122;
  --orange-soft:#f4935a;
  --black:#272727;
  --white:#ffffff;
  --stage:#2b2b2b;
}
*{margin:0;padding:0;box-sizing:border-box}
html,body{width:1200px;height:1200px;overflow:hidden;background:var(--stage)}
.canvas{position:relative;width:1200px;height:1200px}
.card{position:absolute;width:462px;height:808px;overflow:hidden;box-shadow:0 10px 30px rgba(0,0,0,.45)}
.card--front{left:120px;top:164px;background:var(--white)}
.card--back{left:648px;top:163px;background:var(--white)}
.shape-layer{position:absolute;left:0;top:0}
.front-title{position:absolute;top:372px;width:100%;text-align:center;font:700 18px "Montserrat",sans-serif;color:var(--black);letter-spacing:-.2px}
.front-name{position:absolute;top:402px;width:100%;text-align:center;font:400 46px "Permanent Marker",cursive;color:var(--black);letter-spacing:1px}
.front-email{position:absolute;top:478px;width:100%;text-align:center;font:700 23px "Montserrat",sans-serif;color:var(--black)}
.front-brand{position:absolute;top:542px;width:100%;display:flex;justify-content:center;align-items:center;gap:8px;font:700 18px "Roboto",sans-serif;color:var(--orange);letter-spacing:1px}
.dot{display:inline-block;border-radius:50%}
.front-brand .dot{width:16px;height:16px;background:var(--orange)}
.benefits{position:absolute;left:0;top:0;width:100%;height:240px;background:var(--black)}
.benefit{position:absolute;left:50px;display:flex;align-items:center;gap:22px}
.benefit svg{width:44px;height:44px}
.benefit span{font:500 25px "Fira Sans",sans-serif;color:var(--orange);letter-spacing:2.4px}
.offer{position:absolute;left:50px;top:364px;width:360px;text-align:center;font:400 21px/27px "Fira Sans",sans-serif;color:var(--white);letter-spacing:1.3px}
.offer-link{position:absolute;left:52px;top:505px;width:355px;height:46px;display:flex;align-items:center;justify-content:center;gap:10px;font:500 20px "Roboto",sans-serif;color:var(--black)}
.offer-link svg{width:30px;height:30px}
.signoff{position:absolute;left:0;top:620px;width:100%;height:188px;background:var(--orange);text-align:center}
.signoff-mark{display:block;margin:28px auto 0;width:74px;height:74px;background:var(--white)}
.signoff-name{margin-top:14px;font:700 36px "Roboto",sans-serif;color:var(--white);letter-spacing:.5px}
.signoff-tagline{margin-top:2px;font:italic 500 20px "Fira Sans",sans-serif;color:var(--white)}
</style>
</head>
<body>
<div class="canvas">

  <section class="card card--front">
    <svg class="shape-layer" width="462" height="808" viewBox="0 0 462 808">
      <circle cx="70" cy="150" r="130" fill="var(--orange-soft)"/>
      <circle cx="460" cy="40" r="72" fill="var(--orange-soft)"/>
      <polygon points="66,770 392,770 420,808 36,808" fill="var(--orange)"/>
    </svg>
    <p class="front-title">STORY MARKETING COACH</p>
    <h1 class="front-name">DANA HOLLOWAY</h1>
    <p class="front-email">dana@larkwellnow.com</p>
    <p class="front-brand"><span class="dot"></span>LARKWELL</p>
  </section>

  <section class="card card--back">
    <div class="benefits">
      <div class="benefit" style="top:36px">
        <svg viewBox="0 0 44 44"><circle cx="22" cy="9" r="5" fill="var(--orange)"/><path d="M14 22a8 8 0 0 1 16 0z" fill="var(--orange)"/><circle cx="9" cy="28" r="4.5" fill="var(--orange)"/><path d="M1 41a8 8 0 0 1 16 0z" fill="var(--orange)"/><circle cx="35" cy="28" r="4.5" fill="var(--orange)"/><path d="M27 41a8 8 0 0 1 16 0z" fill="var(--orange)"/></svg>
        <span>REACH MORE PEOPLE</span>
      </div>
      <div class="benefit" style="top:96px">
        <svg viewBox="0 0 44 44"><circle cx="22" cy="14" r="11" fill="none" stroke="var(--orange)" stroke-width="3"/><text x="22" y="20" text-anchor="middle" font-family="Roboto,sans-serif" font-weight="700" font-size="16" fill="var(--orange)">$</text><path d="M4 42a18 12 0 0 1 36 0z" fill="var(--orange)"/></svg>
        <span>MAKE MORE MONEY</span>
      </div>
      <div class="benefit" style="top:156px">
        <svg viewBox="0 0 44 44"><circle cx="22" cy="12" r="8" fill="var(--orange)"/><circle cx="12" cy="30" r="8" fill="var(--orange)"/><circle cx="32" cy="30" r="8" fill="var(--orange)"/></svg>
        <span>CREATE MORE IMPACT</span>
      </div>
    </div>

    <svg class="shape-layer" width="462" height="620" viewBox="0 0 462 620">
      <polygon points="20,242 440,242 392,299 64,299" fill="var(--orange)"/>
      <polygon points="0,348 32,363 32,566 0,580" fill="var(--orange)"/>
      <polygon points="462,348 430,363 430,566 462,580" fill="var(--orange)"/>
      <rect x="46" y="361" width="367" height="196" rx="22" fill="var(--black)" stroke="var(--orange)" stroke-width="5"/>
      <rect x="52" y="503" width="355" height="48" rx="18" fill="var(--white)" stroke="var(--orange)" stroke-width="4"/>
    </svg>
    <p class="offer">Get your free Larkwell Starter Package and our marketing guide today at</p>
    <p class="offer-link">
      <svg viewBox="0 0 30 30"><circle cx="15" cy="15" r="12" fill="none" stroke="var(--black)" stroke-width="2"/><ellipse cx="15" cy="15" rx="5" ry="12" fill="none" stroke="var(--black)" stroke-width="1.6"/><line x1="3" y1="15" x2="27" y2="15" stroke="var(--black)" stroke-width="1.6"/><line x1="5" y1="9" x2="25" y2="9" stroke="var(--black)" stroke-width="1.4"/><line x1="5" y1="21" x2="25" y2="21" stroke="var(--black)" stroke-width="1.4"/></svg>
      LARKWELLNOW.COM/START
    </p>

    <div class="signoff">
      <span class="dot signoff-mark"></span>
      <p class="signoff-name">LARKWELL</p>
      <p class="signoff-tagline">Tell Stories that inspire action</p>
    </div>
  </section>

</div>
</body>
</html>
```